Social responsible Renewable Energy company

We at brivoX are an independent power producer company founded in 2021 that handles large scale deployment of Renewable Energy and carbon neutral Energy as a service model. We offer turnkey solutions using solar panel systems and this could be incorporated in our business cards. You can also find our logo in the documents provided. Another key issue is that the business cards will be printed on recicled paper, not sure if this is a limitation in deciding the design. The recycled sign should also be added on the business card and stating that the paper used was recycled. Our website is www.mybrivox-example.com. It should also be very professional, not too dreamy but still needs to capture your imagination. We are really excited to get your ideas !

Target Market(s)

Renewable Energy market

Contact Information for Business Card

The business card will be printed on recycled paper. Name of the company is brivoX. Website is www.mybrivox-example.com

Requirements
Nice to have
• Our motto: Powered by renewable, driven by people.

```html
<!DOCTYPE html>
<html lang="en">
<head>
<meta charset="utf-8">
<title>brivoX business card</title>
<link rel="stylesheet" href="https://fonts.googleapis.com/css2?family=Open+Sans:wght@400;700&display=swap">
<style>
  :root {
    --page-bg: #2a2a2c;
    --card-black: #121213;
    --pattern-dark: #1b1b1d;
    --brand-blue: #2f7fd1;
    --text-light: #e6e6e6;
    --text-muted: #9a9a9e;
  }
  * { margin: 0; padding: 0; box-sizing: border-box; }
  html, body { width: 1200px; height: 900px; overflow: hidden; }
  body {
    background: var(--page-bg);
    font-family: "Open Sans", sans-serif;
    display: flex;
    flex-direction: column;
    align-items: center;
    justify-content: center;
    gap: 40px;
  }
  .card {
    width: 700px;
    height: 400px;
    background: var(--card-black);
    position: relative;
    overflow: hidden;
    box-shadow: 0 12px 30px rgba(0,0,0,.45);
  }
  /* Front */
  .card-front { border-bottom: 8px solid var(--brand-blue); }
  .brand-name {
    position: absolute;
    left: 50px;
    top: 140px;
    font-size: 88px;
    font-weight: 700;
    color: var(--brand-blue);
    letter-spacing: -1px;
    line-height: 1;
  }
  .divider {
    position: absolute;
    left: 375px;
    top: 95px;
    width: 1.5px;
    height: 210px;
    background: var(--brand-blue);
  }
  .contact-block {
    position: absolute;
    left: 395px;
    top: 98px;
    color: var(--text-light);
    font-size: 16px;
    line-height: 1.45;
    white-space: nowrap;
  }
  .person-name {
    color: var(--brand-blue);
    font-weight: 700;
    font-size: 21px;
    text-transform: uppercase;
    line-height: 1.15;
  }
  .person-title { margin-bottom: 14px; }
  .address { margin-bottom: 14px; }
  .contact-line { display: flex; align-items: center; gap: 8px; }
  .contact-line svg { width: 14px; height: 14px; flex: none; fill: var(--brand-blue); }
  /* Back */
  .back-pattern {
    position: absolute;
    inset: 0;
    background: radial-gradient(circle at 50% 40%, #232325, var(--pattern-dark));
  }
  .solar-band {
    position: absolute;
    left: 70px;
    top: 60px;
    width: 120px;
    height: 70px;
  }
  .motto {
    position: absolute;
    left: 70px;
    top: 150px;
    color: var(--text-light);
    font-size: 18px;
    line-height: 1.4;
  }
  .recycled-note {
    position: absolute;
    left: 70px;
    bottom: 62px;
    display: flex;
    align-items: center;
    gap: 10px;
    color: var(--text-muted);
    font-size: 14px;
  }
  .recycled-note svg { width: 26px; height: 26px; flex: none; }
  .back-brand {
    position: absolute;
    right: 70px;
    bottom: 52px;
    font-size: 34px;
    font-weight: 700;
    color: var(--brand-blue);
  }
</style>
</head>
<body>
  <section class="card card-front">
    <div class="brand-name">brivoX</div>
    <div class="divider"></div>
    <div class="contact-block">
      <div class="person-name">Daniel Harrow</div>
      <div class="person-title">President</div>
      <div class="address">1480 Harbor Crest Way<br>Sunvale CA 90000</div>
      <div class="contact-line">
        <svg viewBox="0 0 24 24" aria-hidden="true"><path d="M6.6 10.8a15 15 0 0 0 6.6 6.6l2.2-2.2c.3-.3.7-.4 1-.2 1.1.4 2.3.6 3.6.6.6 0 1 .4 1 1V20c0 .6-.4 1-1 1A17 17 0 0 1 3 4c0-.6.4-1 1-1h3.5c.6 0 1 .4 1 1 0 1.3.2 2.5.6 3.6.1.3 0 .7-.2 1z"/></svg>
        555-010-4821
      </div>
      <div class="contact-line">
        <svg viewBox="0 0 24 24" aria-hidden="true"><path d="M2 5h20v14H2z M2 5l10 8 10-8" fill="none" stroke="#2f7fd1" stroke-width="2.5"/></svg>
        dharrow@mybrivox-example.com
      </div>
      <div class="contact-line">
        <svg viewBox="0 0 24 24" aria-hidden="true"><circle cx="12" cy="12" r="9" fill="none" stroke="#2f7fd1" stroke-width="2.5"/><path d="M3 12h18M12 3c3 3 3 15 0 18M12 3c-3 3-3 15 0 18" fill="none" stroke="#2f7fd1" stroke-width="2"/></svg>
        www.mybrivox-example.com
      </div>
    </div>
  </section>

  <section class="card card-back">
    <div class="back-pattern" role="img" aria-label="Embossed repeating brand symbol pattern in dark grey"></div>
    <svg class="solar-band" viewBox="0 0 120 70" aria-label="Solar panel icon" role="img">
      <circle cx="104" cy="14" r="9" fill="none" stroke="#2f7fd1" stroke-width="2.5"/>
      <path d="M4 66 L22 26 H86 L104 66 Z" fill="none" stroke="#2f7fd1" stroke-width="2.5"/>
      <path d="M13 46 H95 M43 26 L38 66 M65 26 L70 66" stroke="#2f7fd1" stroke-width="2"/>
    </svg>
    <div class="motto">Powered by renewable,<br>driven by people.</div>
    <div class="recycled-note">
      <svg viewBox="0 0 24 24" role="img" aria-label="Recycling arrows icon">
        <g fill="none" stroke="#9a9a9e" stroke-width="2" stroke-linecap="round" stroke-linejoin="round">
          <path d="M12 3 L17 11"/><path d="M14.5 10.5 L17 11 L18 8.6"/>
          <path d="M18 15 H7"/><path d="M9 13 L7 15 L9 17"/>
          <path d="M5 13 L10 5"/><path d="M7.6 5.2 L10 5 L10.8 7.4"/>
        </g>
      </svg>
      Printed on 100% recycled paper
    </div>
    <div class="back-brand">brivoX</div>
  </section>
</body>
</html>
```